Vortel surface design based website for technology jobs website

We need a website design for a technology job listing website, mainly aiming at 20/30/40 year old nerds. Jobs listed from multiple sources will be concatenated and organised. This website will be built with Vortel surface design (https://surfacekit.example/guidelines/) so please use their components. The design should be simple and clear, so a user can directly look for offerings that are interesting for him.

Three different pages will be needed:

1. Main jobs list page

Contains a large table (https://surfacekit.example/guidelines/components/data-tables.html#data-tables-structure), on top or next to this data-table users should be able to apply filters (select countries, select salary ranges) and somewhere an overview of the selected filters should be shown.

- A subscribe bar should be shown somewhere to allow a user to register for weekly/monthly mailings for new job offers with his preferred search filters.

2. Selected item page

If an item is clicked, a user should be able to view a job posting and it's details.

3. An advertiser should be able post his job offer.
Similar fields as https://post.ledgerworkboard.example/.
(https://surfacekit.example/guidelines/components/text-fields.html#text-fields-layout)

Target Market(s)

20/30/40 year old nerds.

Industry/Entity Type

Computer

Logo Text

TechHirePlaza.example

Number of Pages Required

3 page

Colors

Designer to choose colors to be used in the design.

Requirements
Must have
• 1. Main jobs list page
• Contains a large table (https://surfacekit.example/guidelines/components/data-tables.html#data-tables-structure), on top or next to this data-table users should be able to apply filters (select countries, select salary ranges) and somewhere an overview of the selected filters should be shown.
• - A subscribe bar should be shown somewhere to allow a user to register for weekly/monthly mailings for new job offers with his preferred search filters.
• 2. Selected item page
• If an item is clicked, a user should be able to view a job posting and it's details.
• 3. An advertiser should be able post his job offer,
• (https://surfacekit.example/guidelines/components/text-fields.html#text-fields-layout)
• Please use open fonts!

```html
<!DOCTYPE html>
<html lang="en">
<head>
<meta charset="utf-8">
<title>Post Your Job</title>
<link href="https://fonts.googleapis.com/css2?family=Roboto:wght@400;500&display=swap" rel="stylesheet">
<style>
:root{
  --page-bg:#eeeeee;
  --hero-dark:#06122a;
  --hero-mid:#0b2a55;
  --search-bar:#08a9f2;
  --search-btn:#0d5aa0;
  --card:#ffffff;
  --ink:#212121;
  --label:#616161;
  --hint:#9e9e9e;
  --line:#8a8a8a;
  --focus:#0d5aa0;
  --accent:#08a9f2;
  --fab:#e0392f;
  --footer:#37393c;
}
*{box-sizing:border-box;margin:0;padding:0}
html,body{width:1038px;height:1200px;overflow:hidden}
body{position:relative;background:var(--page-bg);font-family:'Roboto',sans-serif;color:var(--ink)}
.hero{position:absolute;left:0;top:0;width:1038px;height:344px;
  background:radial-gradient(ellipse at 30% 40%,#1b4f8f 0%,var(--hero-mid) 35%,var(--hero-dark) 80%)}
.menu-icon{position:absolute;left:74px;top:19px}
.brand{position:absolute;left:0;width:1038px;top:14px;text-align:center;color:#fff;font-size:27px;font-weight:500}
.search-bar{position:absolute;left:74px;top:91px;width:889px;height:84px;background:var(--search-bar)}
.search-field{position:absolute;top:24px;height:35px;background:#fff;border-radius:2px;
  font-size:11px;color:var(--hint);padding:0 6px;line-height:35px;white-space:nowrap;overflow:hidden}
.search-field svg{position:absolute;right:7px;top:14px}
.search-btn{position:absolute;left:776px;top:24px;width:88px;height:35px;background:var(--search-btn);border-radius:2px}
.search-btn svg{position:absolute;left:35px;top:9px}
.card{position:absolute;left:74px;top:231px;width:889px;height:892px;background:var(--card);box-shadow:0 1px 4px rgba(0,0,0,.2)}
.heading{position:absolute;font-size:15px;font-weight:400;color:var(--ink);white-space:nowrap}
.field{position:absolute;left:234px;width:570px;border-bottom:1px solid var(--line)}
.field .label{position:absolute;left:0;font-size:10.5px;color:var(--label);white-space:nowrap}
.field.active{border-bottom:2px solid var(--focus)}
.field.active .label{color:var(--focus);font-size:9px;font-weight:500}
.field.half{width:324px}
.logo-drop{position:absolute;left:580px;top:614px;width:223px;height:110px;border:1px solid #dcdcdc}
.logo-drop svg{position:absolute;left:94px;top:30px}
.small-label{position:absolute;font-size:10.5px;color:var(--label)}
.photo-drop{position:absolute;left:232px;top:872px;width:78px;height:78px;border:1px solid #bdbdbd;border-radius:50%}
.photo-drop svg{position:absolute;left:21px;top:15px}
.post-btn{position:absolute;left:234px;top:1049px;width:142px;height:34px;background:var(--accent);color:#fff;
  font-size:11px;font-weight:500;text-align:center;line-height:34px;border-radius:2px}
.fab{position:absolute;left:974px;top:1071px;width:52px;height:52px;border-radius:50%;background:var(--fab);box-shadow:0 2px 5px rgba(0,0,0,.3)}
.fab svg{position:absolute;left:16px;top:16px}
.footer{position:absolute;left:0;top:1165px;width:1038px;height:35px;background:var(--footer);color:#fff;
  font-size:10px;text-align:center;line-height:35px}
</style>
</head>
<body>
<div class="hero" role="img" aria-label="Dark blue abstract network of connected glowing lines"></div>
<svg class="menu-icon" width="21" height="15" viewBox="0 0 21 15"><rect y="0" width="21" height="2" fill="#fff"/><rect y="6" width="21" height="2" fill="#fff"/><rect y="12" width="21" height="2" fill="#fff"/></svg>
<div class="brand">Logo Name</div>

<div class="search-bar">
  <div class="search-field" style="left:26px;width:252px">Keyword e.g. ( jobTitle, Description,Tags)<svg width="8" height="5" viewBox="0 0 8 5"><path d="M1 1l3 3 3-3" stroke="#777" fill="none"/></svg></div>
  <div class="search-field" style="left:286px;width:186px">Select Location<svg width="8" height="5" viewBox="0 0 8 5"><path d="M1 1l3 3 3-3" stroke="#777" fill="none"/></svg></div>
  <div class="search-field" style="left:479px;width:185px;color:var(--label)">Salary<svg width="8" height="5" viewBox="0 0 8 5"><path d="M1 1l3 3 3-3" stroke="#777" fill="none"/></svg></div>
  <div class="search-field" style="left:671px;width:98px;color:var(--label)">Designation<svg width="8" height="5" viewBox="0 0 8 5"><path d="M1 1l3 3 3-3" stroke="#777" fill="none"/></svg></div>
  <div class="search-btn"><svg width="18" height="18" viewBox="0 0 18 18"><circle cx="7.5" cy="7.5" r="5.5" stroke="#fff" stroke-width="2.4" fill="none"/><path d="M11.5 11.5l5 5" stroke="#fff" stroke-width="2.8" stroke-linecap="round"/></svg></div>
</div>

<div class="card"></div>

<div class="heading" style="left:233px;top:270px">Job Details</div>
<div class="field active" style="top:308px;height:35px"><span class="label" style="top:0">Title&nbsp;&nbsp;*</span></div>
<div class="field" style="top:376px;height:21px"><span class="label" style="top:0">Location</span></div>
<div class="field" style="top:430px;height:21px"><span class="label" style="top:0">City</span></div>
<div class="field" style="top:484px;height:59px"><span class="label" style="top:0">Description</span></div>

<div class="heading" style="left:235px;top:576px">Your Company Details?</div>
<div class="field half" style="top:611px;height:20px"><span class="label" style="top:0">Company Name</span></div>
<div class="field half" style="top:665px;height:21px"><span class="label" style="top:0">Website</span></div>
<div class="field half" style="top:721px;height:21px"><span class="label" style="top:0">Social Profile</span></div>
<div class="logo-drop"><svg width="36" height="38" viewBox="0 0 36 38"><path d="M14 6l4-4 4 4" stroke="#ccc" stroke-width="2" fill="none"/><rect x="0" y="8" width="36" height="30" fill="#d6d6d6"/><rect x="4" y="12" width="28" height="22" fill="#f2f2f2"/><path d="M6 32l9-10 6 6 4-4 6 8z" fill="#c4c4c4"/><circle cx="25" cy="17" r="2.5" fill="#c4c4c4"/></svg></div>
<div class="small-label" style="left:580px;top:730px">Logo</div>

<div class="heading" style="left:234px;top:774px">Let's get personal</div>
<div class="field" style="top:812px;height:21px"><span class="label" style="top:0">Your or Your Boss Name</span></div>
<div class="photo-drop"><svg width="36" height="38" viewBox="0 0 36 38"><path d="M14 6l4-4 4 4" stroke="#ccc" stroke-width="2" fill="none"/><rect x="0" y="8" width="36" height="30" fill="#d6d6d6"/><rect x="4" y="12" width="28" height="22" fill="#f2f2f2"/><path d="M6 32l9-10 6 6 4-4 6 8z" fill="#c4c4c4"/><circle cx="25" cy="17" r="2.5" fill="#c4c4c4"/></svg></div>
<div class="small-label" style="left:328px;top:904px;color:var(--hint)">Photo</div>
<div class="field" style="top:990px;height:21px"><span class="label" style="top:0">Send application to</span></div>

<div class="post-btn">Post Your Job</div>

<div class="fab"><svg width="20" height="20" viewBox="0 0 20 20"><path d="M10 2v16M2 10h16" stroke="#fff" stroke-width="2"/></svg></div>

<div class="footer">Copyright © website address I All Rights Reaserved</div>
</body>
</html>
```